Shine Fox Auto Care Business Card

2 side business card design for an auto detailing business

Target Market(s)

Auto detailing

Contact Information for Business Card

Things included

The business name “Shine Fox Auto Care”
Mark Dunrow
(403)271-6094
Alderwick, Sk

Services offered - complete interior& exterior detail
- paint correction & protection
- ceramic coating
- trim restore
- auto carpet & seat cleaning

Requirements
Must have
• Colours that are in my logo

Services offered

My name Mark Dunrow
403-271-6094
Alderwick, Sk

Not too sure in what order for these ?
Website. Shinefoxautocare.com
Instagram Shinefoxautocare
Email. Shinefoxautoac@mailvento.com

```html
<!DOCTYPE html>
<html lang="en">
<head>
<meta charset="utf-8">
<title>Shine Fox Auto Care – Business Card</title>
<link href="https://fonts.googleapis.com/css2?family=Arimo:wght@400;700&display=swap" rel="stylesheet">
<style>
  :root {
    --page-bg: #1c1c1c;
    --card-bg: #0b0b0b;
    --card-edge: #1a1a1a;
    --red: #b3141a;
    --white: #f4f4f4;
    --divider: #2e2e2e;
  }
  * { box-sizing: border-box; margin: 0; padding: 0; }
  html, body {
    width: 1200px; height: 900px; overflow: hidden;
    background: var(--page-bg);
    font-family: "Arimo", Arial, sans-serif;
  }
  .canvas {
    width: 1200px; height: 900px;
    display: flex; flex-direction: column;
    align-items: center; justify-content: center; gap: 44px;
  }
  .card {
    width: 630px; height: 360px;
    background: var(--card-bg);
    border: 1px solid var(--card-edge);
    box-shadow: 0 10px 30px rgba(0,0,0,.55);
    position: relative; overflow: hidden;
  }

  /* brand lockup */
  .brand { display: flex; align-items: center; gap: 14px; }
  .brand-mark {
    border: 6px solid var(--red); border-radius: 50%;
    flex: none;
  }
  .brand-name {
    color: var(--white); font-weight: 700;
    text-transform: uppercase; letter-spacing: .04em; line-height: 1.05;
  }

  /* contact side */
  .card--contact { display: flex; }
  .contact-brand {
    width: 270px; border-right: 1px solid var(--divider);
    display: flex; align-items: center; justify-content: center;
  }
  .contact-brand .brand { flex-direction: column; gap: 16px; text-align: center; }
  .contact-brand .brand-mark { width: 96px; height: 96px; }
  .contact-brand .brand-name { font-size: 26px; }
  .contact-info { padding: 70px 20px 0 30px; }
  .person-name {
    color: var(--red); font-weight: 700; font-size: 24px;
    text-transform: uppercase; letter-spacing: .01em; margin-bottom: 22px;
  }
  .contact-list { list-style: none; }
  .contact-list li {
    display: flex; align-items: center; gap: 12px;
    color: var(--white); font-size: 16px; margin-bottom: 12px;
    white-space: nowrap;
  }
  .contact-list li.contact-location { margin-top: 22px; }
  .contact-icon { width: 22px; height: 22px; flex: none; }

  /* services side */
  .card--services { padding: 46px 0 0 70px; }
  .card--services .brand-mark { width: 100px; height: 100px; border-width: 7px; }
  .card--services .brand-name { font-size: 34px; }
  .services-heading {
    color: var(--red); font-weight: 700; font-size: 22px;
    text-transform: uppercase; margin: 26px 0 4px;
  }
  .services-sub {
    color: var(--white); font-size: 15px; text-transform: uppercase; margin-bottom: 22px;
  }
  .services-list {
    list-style: none; display: grid;
    grid-template-columns: 280px 200px; row-gap: 8px;
  }
  .services-list li {
    display: flex; align-items: center; gap: 8px;
    color: var(--white); font-size: 17px; white-space: nowrap;
  }
  .service-dot {
    width: 12px; height: 12px; border: 2px solid var(--red); border-radius: 50%; flex: none;
  }
</style>
</head>
<body>
<main class="canvas">

  <section class="card card--contact" aria-label="Business card, contact side">
    <div class="contact-brand">
      <div class="brand">
        <span class="brand-mark"></span>
        <span class="brand-name">Shine Fox<br>Auto Care</span>
      </div>
    </div>
    <div class="contact-info">
      <h1 class="person-name">Mark Dunrow</h1>
      <ul class="contact-list">
        <li>
          <svg class="contact-icon" viewBox="0 0 22 22" aria-hidden="true"><circle cx="11" cy="11" r="11" fill="var(--red)"/><path d="M7 6.5l2 -.5 1.2 2.6-1.2 1a6 6 0 0 0 3.4 3.4l1-1.2 2.6 1.2-.5 2c-4.5 .3-8.8-4-8.5-8.5z" fill="#fff"/></svg>
          (403)271-6094
        </li>
        <li>
          <svg class="contact-icon" viewBox="0 0 22 22" aria-hidden="true"><circle cx="11" cy="11" r="11" fill="var(--red)"/><rect x="5.5" y="7.5" width="11" height="7.5" fill="#fff"/><path d="M5.5 7.5l5.5 4.2 5.5-4.2" fill="none" stroke="var(--red)" stroke-width="1.2"/></svg>
          Shinefoxautocare@mailvento.com
        </li>
        <li>
          <svg class="contact-icon" viewBox="0 0 22 22" aria-hidden="true"><circle cx="11" cy="11" r="11" fill="var(--red)"/><g fill="none" stroke="#fff" stroke-width="1.2"><circle cx="11" cy="11" r="5.5"/><ellipse cx="11" cy="11" rx="2.4" ry="5.5"/><path d="M5.5 11h11"/></g></svg>
          www.Shinefoxautocare.com
        </li>
        <li>
          <svg class="contact-icon" viewBox="0 0 22 22" aria-hidden="true"><circle cx="11" cy="11" r="11" fill="var(--red)"/><circle cx="11" cy="11" r="4.5" fill="none" stroke="#fff" stroke-width="1.4"/></svg>
          Shinefoxautocare
        </li>
        <li class="contact-location">
          <svg class="contact-icon" viewBox="0 0 22 22" aria-hidden="true"><circle cx="11" cy="11" r="11" fill="var(--red)"/><path d="M11 17s-4.5-4.6-4.5-7.5a4.5 4.5 0 0 1 9 0C15.5 12.4 11 17 11 17z" fill="#fff"/><circle cx="11" cy="9.5" r="1.6" fill="var(--red)"/></svg>
          Alderwick, Sk
        </li>
      </ul>
    </div>
  </section>

  <section class="card card--services" aria-label="Business card, services side">
    <div class="brand">
      <span class="brand-mark"></span>
      <span class="brand-name">Shine Fox<br>Auto Care</span>
    </div>
    <h2 class="services-heading">Services Offered</h2>
    <p class="services-sub">Complete interior &amp; exterior detail</p>
    <ul class="services-list">
      <li><span class="service-dot"></span>Paint correction &amp; protection</li>
      <li><span class="service-dot"></span>Ceramic coating</li>
      <li><span class="service-dot"></span>Auto carpet &amp; seat cleaning</li>
      <li><span class="service-dot"></span>Trim restore</li>
    </ul>
  </section>

</main>
</body>
</html>
```